Interior Design/ New Construction interior finishes

Interior Design Website

Target Market(s)

Home builders, New Construction, Renovations, Public

Industry/Entity Type

Construction

Coding

Coded - Design and coding required

Number of Pages Required

1 page

Font styles to use
Sans Serif

Colors

Designer to choose colors to be used in the design.

Requirements
Must have
• Section to upload pictures of projects
• Simple and modern design
• Designer 1 details about myself
• Logo
• Upload section for photos for future jobs
Nice to have
• Sections they can click on to see certain rooms in a house
• Decorating, floral arrangements, holiday decorating.
• I have lots of before and after as well. Maybe a section for those.

```html
<!DOCTYPE html>
<html lang="en">
<head>
<meta charset="utf-8">
<title>Lumen Interiors — Interior Design</title>
<link rel="stylesheet" href="https://fonts.googleapis.com/css2?family=Montserrat:wght@400;500;600&family=Open+Sans:ital,wght@0,400;0,600;1,400&display=swap">
<style>
:root{
  --ink:#1c1c1c;
  --text:#333333;
  --muted:#6a6a6a;
  --line:#8a8a8a;
  --white:#ffffff;
  --dark:#262626;
  --darker:#1a1a1a;
  --footer:#dcdcdc;
  --label:#4a4a4a;
  --card-border:#9a9a9a;
  --cream:#e9e1d8;
}
*{box-sizing:border-box;margin:0;padding:0}
html,body{width:1200px;height:2980px;overflow:hidden;background:var(--white)}
body{position:relative;font-family:"Open Sans",Arial,sans-serif;color:var(--text)}
.abs{position:absolute}
.heading{font-family:"Montserrat",Arial,sans-serif;font-weight:400;text-align:center}

/* header */
.site-header{left:0;top:0;width:1200px;height:90px;background:var(--white)}
.brand{left:122px;top:8px;height:80px;display:flex;align-items:center;gap:16px}
.brand-dot{width:80px;height:80px;border-radius:50%;border:3px solid var(--ink);background:var(--white);flex:none}
.brand-name{font-family:"Montserrat",Arial,sans-serif;font-size:24px;letter-spacing:2px;color:var(--ink);font-weight:400;white-space:nowrap}
.main-nav{left:500px;top:0;height:90px;display:flex;align-items:center;gap:34px;font-family:"Montserrat",Arial,sans-serif;font-size:15px;color:var(--ink);white-space:nowrap}
.main-nav .active{border:2px solid #cfcfcf;border-radius:50%;padding:22px 12px}

/* hero */
.hero{left:0;top:90px;width:1200px;height:550px;background:linear-gradient(180deg,#dcdad6 0%,#b9b2a8 45%,#7a6a58 80%,#55483c 100%)}
.hero-title{left:0;top:280px;width:1200px;color:var(--white);font-family:"Montserrat",Arial,sans-serif;font-weight:600;font-size:42px;line-height:50px;text-align:center;letter-spacing:1px}
.hero-rule{left:248px;width:722px;height:2px;background:rgba(255,255,255,.8)}
.arrow{width:48px;height:48px;border-radius:50%;border:2px solid currentColor;display:flex;align-items:center;justify-content:center}
.arrow svg{width:18px;height:18px}

/* welcome */
.welcome{left:0;top:640px;width:1200px;height:760px}
.welcome-title{left:0;top:700px;width:1200px;font-size:36px;color:var(--white)}
.divider{display:flex;align-items:center;gap:12px;justify-content:center}
.divider span.rule{width:170px;height:1px;background:currentColor}
.divider span.dot{width:30px;height:30px;border-radius:50%;border:1.5px solid currentColor}
.welcome-copy{left:210px;top:790px;width:780px;color:#e0e0e0;font-size:15px;line-height:26px;text-align:center}
.service{width:330px;text-align:center}
.service-photo{width:232px;height:232px;border-radius:50%;border:3px solid #d8d8d8;box-shadow:0 0 0 3px #555;margin:0 auto}
.service h3{font-family:"Montserrat",Arial,sans-serif;font-weight:500;font-size:22px;color:var(--ink);margin-top:18px}
.service p{font-size:12px;line-height:20px;color:var(--muted);margin:10px auto 0;width:240px}
.btn{display:inline-block;border:2px solid var(--ink);border-radius:20px;padding:8px 26px;font-family:"Montserrat",Arial,sans-serif;font-size:13px;color:var(--ink);margin-top:22px}

/* gallery */
.section-title{font-size:32px;color:var(--ink);left:0;width:1200px}
.pair{top:1528px;width:474px;height:246px}
.pair-photos{display:flex;height:206px}
.pair-photos div{flex:1}
.pair-labels{display:flex;height:40px;background:var(--label)}
.pair-labels span{flex:1;color:var(--white);font-family:"Montserrat",Arial,sans-serif;font-size:15px;display:flex;align-items:center;justify-content:center}
.pair-labels span+span{background:#3a3a3a}

/* why */
.why{left:0;top:1834px;width:1200px;height:462px;background:linear-gradient(90deg,#a79b92 0%,#d7d0cb 50%,#ede9e6 75%,#cfcac6 100%)}
.why h2{font-family:"Montserrat",Arial,sans-serif;font-weight:400;font-size:28px;color:var(--white)}
.why p{color:#e6e6e6}

/* testimonials */
.quote-card{top:2456px;width:314px;height:196px;border:2px solid var(--card-border);background:var(--white);box-shadow:0 2px 4px rgba(0,0,0,.2);text-align:center;padding:20px 24px 0}
.quote-mark{font-family:Georgia,serif;font-size:52px;line-height:40px;color:#9a9a9a;height:40px}
.quote-card p{font-style:italic;font-size:12.5px;line-height:23px;color:var(--muted);margin-top:8px}
.author{top:2664px;display:flex;align-items:center;gap:8px}
.avatar{width:46px;height:46px;border-radius:50%;background:linear-gradient(135deg,#c8b6a6,#7b6a5c)}
.author strong{display:block;font-weight:400;font-size:16px;color:var(--text);font-family:"Montserrat",Arial,sans-serif}
.author small{font-size:11px;color:var(--muted)}

/* footer */
.site-footer{left:0;top:2796px;width:1200px;height:184px;background:var(--footer)}
.footer-nav{left:0;top:2838px;width:1200px;display:flex;justify-content:center;gap:34px;font-family:"Montserrat",Arial,sans-serif;font-size:15px;color:var(--ink)}
.copyright{left:0;top:2874px;width:1200px;text-align:center;font-size:11px;color:var(--muted)}
.social{left:0;top:2912px;width:1200px;display:flex;justify-content:center;gap:10px}
.social span{width:38px;height:38px;border-radius:50%;border:2px solid var(--ink)}
</style>
</head>
<body>

<header class="site-header abs">
  <div class="brand abs"><span class="brand-dot"></span><span class="brand-name">Lumen Interiors</span></div>
  <nav class="main-nav abs">
    <span class="active">Home</span><span>About Us</span><span>Services</span><span>Before &amp; After Gallery</span><span>Contact Us</span>
  </nav>
</header>

<section class="hero abs" role="img" aria-label="Bright living room with white armchairs and a rustic wooden coffee table"></section>
<div class="hero-rule abs" style="top:270px"></div>
<h1 class="hero-title abs">HOLIDAY DECORATING<br>AND FLORAL ARRANGEMENTS</h1>
<div class="hero-rule abs" style="top:390px"></div>
<div class="arrow abs" style="left:64px;top:300px;color:var(--white)"><svg viewBox="0 0 18 18"><path d="M12 2 5 9l7 7" fill="none" stroke="currentColor" stroke-width="2.5"/></svg></div>
<div class="arrow abs" style="left:1078px;top:300px;color:var(--white)"><svg viewBox="0 0 18 18"><path d="M6 2l7 7-7 7" fill="none" stroke="currentColor" stroke-width="2.5"/></svg></div>

<svg class="welcome abs" viewBox="0 0 1200 760" role="img" aria-label="Dark patio view fading into a light dining room interior">
  <defs>
    <linearGradient id="darkBand" x1="0" y1="0" x2="0" y2="1"><stop offset="0" stop-color="#2a2a2a"/><stop offset="1" stop-color="#3d3b39"/></linearGradient>
    <linearGradient id="lightBand" x1="0" y1="0" x2="0" y2="1"><stop offset="0" stop-color="#d9d0c6"/><stop offset="1" stop-color="#f1ece7"/></linearGradient>
  </defs>
  <rect width="1200" height="760" fill="url(#lightBand)"/>
  <path d="M0 0H1200V200C1050 270 900 300 700 300C480 300 300 360 180 440C110 490 50 500 0 500Z" fill="url(#darkBand)"/>
</svg>
<h2 class="welcome-title heading abs">Welcome to Lumen Interiors</h2>
<div class="divider abs" style="left:0;top:752px;width:1200px;color:#9a9a9a"><span class="rule"></span><span class="dot"></span><span class="rule"></span></div>
<p class="welcome-copy abs">Maecenas aliquet velit vel turpis Mauris neque metus malesuada nec ultricies sit amet porttitor mattis enim In massa libero interdum nec interdum vel blandit sed nulla In ullamcorper est eget tempor cursus neque mi consectetuer mi a ultricies massa est sed nisl Class aptent taciti sociosqu</p>

<div class="service abs" style="left:103px;top:944px">
  <div class="service-photo" role="img" aria-label="Decorated living room with chandelier" style="background:radial-gradient(circle,#c79a6a,#6b3d25)"></div>
  <h3>Decorating</h3><p>Arper est eget tempor cursus neque mi consectetuer mi a ultricies</p><span class="btn">READ MORE</span>
</div>
<div class="service abs" style="left:436px;top:944px">
  <div class="service-photo" role="img" aria-label="Purple floral arrangement on stacked books" style="background:radial-gradient(circle,#e8e4ec,#8f80a8)"></div>
  <h3>Floral Arrangements</h3><p>Arper est eget tempor cursus neque mi consectetuer mi a ultricies</p><span class="btn">READ MORE</span>
</div>
<div class="service abs" style="left:772px;top:944px">
  <div class="service-photo" role="img" aria-label="Holiday decorated lounge with crystal chandelier" style="background:radial-gradient(circle,#8a7f72,#2e3440)"></div>
  <h3>Holiday Decorating</h3><p>Arper est eget tempor cursus neque mi consectetuer mi a ultricies</p><span class="btn">READ MORE</span>
</div>

<h2 class="section-title heading abs" style="top:1428px">Before &amp; After Gallery</h2>
<div class="divider abs" style="left:0;top:1476px;width:1200px;color:var(--line)"><span class="rule" style="width:175px"></span><span class="dot"></span><span class="rule" style="width:175px"></span></div>
<div class="arrow abs" style="left:58px;top:1620px;color:var(--ink)"><svg viewBox="0 0 18 18"><path d="M12 2 5 9l7 7" fill="none" stroke="currentColor" stroke-width="2.5"/></svg></div>
<div class="arrow abs" style="left:1092px;top:1620px;color:var(--ink)"><svg viewBox="0 0 18 18"><path d="M6 2l7 7-7 7" fill="none" stroke="currentColor" stroke-width="2.5"/></svg></div>
<div class="pair abs" style="left:118px">
  <div class="pair-photos"><div role="img" aria-label="White living room before" style="background:linear-gradient(135deg,#f4f4f2,#d6d4cf)"></div><div role="img" aria-label="Kitchen with island after" style="background:linear-gradient(135deg,#e8e6e2,#8c7d6c)"></div></div>
  <div class="pair-labels"><span>BEFORE</span><span>AFTER</span></div>
</div>
<div class="pair abs" style="left:608px">
  <div class="pair-photos"><div role="img" aria-label="Marble sitting room before" style="background:linear-gradient(135deg,#cfc8bc,#5e5448)"></div><div role="img" aria-label="Open living room with blue sofa after" style="background:linear-gradient(135deg,#eceae6,#3f4a5a)"></div></div>
  <div class="pair-labels"><span>BEFORE</span><span>AFTER</span></div>
</div>

<section class="why abs" role="img" aria-label="Modern bathroom with starburst chandelier and marble walls">
  <svg class="abs" style="left:0;top:0" width="540" height="462" viewBox="0 0 540 462"><path d="M0 0H380C520 130 560 330 440 462H0Z" fill="rgba(26,26,26,.9)"/></svg>
</section>
<div class="abs" style="left:128px;top:1944px;width:360px">
  <div class="why" style="position:static;background:none;width:auto;height:auto">
    <h2>Why Choose Us</h2>
    <p style="font-size:15px;line-height:24px;margin-top:18px">Anterdum vel blandit sed nulla In ullamcorper est eget tempor cursus neque mi consecte</p>
    <p style="font-size:13px;line-height:23px;margin-top:16px">Class aptent taciti sociosqu ad litora torquent per conubia nostra per inceptos hymenaeos Proin nulla arcu nonummy luctus dictum eget fermentum et lor</p>
    <span class="btn" style="border-color:var(--white);color:var(--white);margin-top:18px;padding:8px 34px">READ MORE</span>
  </div>
</div>

<h2 class="section-title heading abs" style="top:2354px;font-size:30px">What Our Customer Says</h2>
<div class="divider abs" style="left:0;top:2402px;width:1200px;color:var(--line)"><span class="rule" style="width:160px"></span><span class="dot"></span><span class="rule" style="width:160px"></span></div>

<div class="quote-card abs" style="left:120px"><div class="quote-mark">&ldquo;</div><p>In ullamcorper est eget tempor cursus neque mi consectetuer mi a ultricies massa est sed nisl Class aptent taciti sociosqu ad litora torquent per conubia nostra</p></div>
<div class="quote-card abs" style="left:444px"><div class="quote-mark">&ldquo;</div><p>In ullamcorper est eget tempor cursus neque mi consectetuer mi a ultricies massa est sed nisl Class aptent taciti sociosqu ad litora torquent per conubia nostra</p></div>
<div class="quote-card abs" style="left:772px"><div class="quote-mark">&ldquo;</div><p>In ullamcorper est eget tempor cursus neque mi consectetuer mi a ultricies massa est sed nisl Class aptent taciti sociosqu ad litora torquent per conubia nostra</p></div>

<div class="author abs" style="left:198px"><span class="avatar" role="img" aria-label="Customer portrait"></span><div><strong>By Author Name</strong><small>City, Location</small></div></div>
<div class="author abs" style="left:518px"><span class="avatar" role="img" aria-label="Customer portrait"></span><div><strong>By Author Name</strong><small>City, Location</small></div></div>
<div class="author abs" style="left:852px"><span class="avatar" role="img" aria-label="Customer portrait"></span><div><strong>By Author Name</strong><small>City, Location</small></div></div>

<footer class="site-footer abs"></footer>
<nav class="footer-nav abs"><span>HOME</span><span>ABOUT US</span><span>SERVICES</span><span>BEFORE &amp; AFTER GALLERY</span><span>CONTACT US</span></nav>
<p class="copyright abs">© 2018 Company Name  All right reserved</p>
<div class="social abs" aria-label="Social links"><span></span><span></span><span></span><span></span></div>

</body>
</html>
```